Social responsible Renewable Energy company

We at brivoX are an independent power producer company founded in 2021 that handles large scale deployment of Renewable Energy and carbon neutral Energy as a service model. We offer turnkey solutions using solar panel systems and this could be incorporated in our business cards. You can also find our logo in the documents provided. Another key issue is that the business cards will be printed on recicled paper, not sure if this is a limitation in deciding the design. The recycled sign should also be added on the business card and stating that the paper used was recycled. Our website is www.mybrivox-example.com. It should also be very professional, not too dreamy but still needs to capture your imagination. We are really excited to get your ideas !

Target Market(s)

Renewable Energy market

Contact Information for Business Card

The business card will be printed on recycled paper. Name of the company is brivoX. Website is www.mybrivox-example.com

Requirements
Nice to have
• Our motto: Powered by renewable, driven by people.

```html
<!DOCTYPE html>
<html lang="en">
<head>
<meta charset="UTF-8">
<title>brivoX business cards</title>
<link href="https://fonts.googleapis.com/css2?family=Montserrat:wght@400;500;700&display=swap" rel="stylesheet">
<style>
  :root {
    --navy: #0b3f8a;
    --blue: #1f64c0;
    --green: #7cc242;
    --badge: #2b5a2a;
    --paper: #ffffff;
    --ground: #eeeeec;
    --note: #555555;
  }
  * { margin: 0; padding: 0; box-sizing: border-box; }
  html, body { width: 1200px; height: 1200px; overflow: hidden; }
  body {
    background: var(--ground);
    font-family: "Montserrat", sans-serif;
    position: relative;
  }
  .card {
    position: absolute;
    left: 320px;
    width: 560px;
    height: 320px;
    background: var(--paper);
    box-shadow: 0 8px 24px rgba(0,0,0,0.12);
    overflow: hidden;
  }
  .card--front { top: 50px; }
  .card--back { top: 410px; }

  .wordmark {
    display: flex;
    align-items: center;
    gap: 8px;
    color: var(--navy);
    font-weight: 700;
    letter-spacing: 1px;
    line-height: 1;
  }
  .wordmark__dot { border-radius: 50%; background: var(--blue); }
  .card--front .wordmark {
    position: absolute;
    top: 80px; left: 0; right: 0;
    justify-content: center;
    font-size: 64px;
  }
  .card--front .wordmark__dot { width: 26px; height: 26px; }
  .recycled-badge {
    position: absolute;
    top: 170px; left: 248px;
    width: 64px; height: 40px;
    background: var(--badge);
    border-radius: 2px;
  }
  .card--front .site {
    position: absolute;
    top: 240px; left: 0; right: 0;
    text-align: center;
    color: var(--green);
    font-size: 17px;
    font-weight: 500;
  }

  .card--back .wordmark {
    position: absolute;
    top: 44px; right: 40px;
    font-size: 34px;
  }
  .card--back .wordmark__dot { width: 14px; height: 14px; }
  .person { position: absolute; top: 134px; left: 32px; color: var(--navy); }
  .person__name { font-size: 20px; font-weight: 700; line-height: 1.2; }
  .person__role { font-size: 12px; font-weight: 500; margin-top: 2px; }
  .divider { position: absolute; left: 0; top: 0; }
  .solar-panel {
    position: absolute;
    left: 462px; top: 152px;
    width: 60px; height: 36px;
    background: linear-gradient(135deg, #6fb6e8, #2a7cc4);
  }
  .contact {
    position: absolute;
    font-size: 12px;
    color: var(--navy);
    list-style: none;
  }
  .contact li { display: flex; align-items: flex-start; gap: 8px; margin-bottom: 7px; line-height: 1.35; }
  .contact svg { flex: none; margin-top: 2px; }
  .contact--personal { top: 214px; left: 32px; }
  .contact--company { top: 214px; left: 286px; }
  .stripes { position: absolute; right: 0; bottom: 0; }

  .production-notes {
    position: absolute;
    left: 42px; top: 922px;
    color: var(--note);
    font-size: 22px;
    font-weight: 400;
    line-height: 1.14;
  }
</style>
</head>
<body>

<section class="card card--front">
  <div class="wordmark"><span>brivoX</span><span class="wordmark__dot"></span></div>
  <div class="recycled-badge" role="img" aria-label="Recycled paper certification badge"></div>
  <p class="site">www.mybrivox-example.com</p>
</section>

<section class="card card--back">
  <div class="wordmark"><span>brivoX</span><span class="wordmark__dot"></span></div>
  <div class="person">
    <p class="person__name">Dara Holm</p>
    <p class="person__role">CEO</p>
  </div>
  <svg class="divider" width="560" height="320" aria-hidden="true">
    <line x1="70" y1="196" x2="470" y2="196" stroke="#1f64c0" stroke-width="1"/>
    <line x1="470" y1="188" x2="470" y2="196" stroke="#1f64c0" stroke-width="1.5"/>
  </svg>
  <div class="solar-panel" role="img" aria-label="Solar panel illustration"></div>
  <ul class="contact contact--personal">
    <li>
      <svg width="12" height="12" viewBox="0 0 12 12"><path d="M3 1 L5 3.5 L4 5 Q5 7 7 8 L8.5 7 L11 9 L9.5 11 Q4 10.5 1 2.5 Z" fill="none" stroke="#0b3f8a" stroke-width="1"/></svg>
      <span>555 010-2746</span>
    </li>
    <li>
      <svg width="12" height="12" viewBox="0 0 12 12"><rect x="1" y="2.5" width="10" height="7" fill="none" stroke="#0b3f8a"/><path d="M1 2.5 L6 6.5 L11 2.5" fill="none" stroke="#0b3f8a"/></svg>
      <span>info@mybrivox-example.com</span>
    </li>
  </ul>
  <ul class="contact contact--company">
    <li>
      <svg width="12" height="12" viewBox="0 0 12 12"><circle cx="6" cy="6" r="5" fill="none" stroke="#0b3f8a"/><ellipse cx="6" cy="6" rx="2.2" ry="5" fill="none" stroke="#0b3f8a"/><line x1="1" y1="6" x2="11" y2="6" stroke="#0b3f8a"/></svg>
      <span>www.mybrivox-example.com</span>
    </li>
    <li>
      <svg width="12" height="12" viewBox="0 0 12 12"><path d="M1.5 6 L6 1.5 L10.5 6 M2.5 5 V10.5 H9.5 V5" fill="none" stroke="#0b3f8a"/></svg>
      <span>48 Volta Lane, Suite 200,<br>GA 30999</span>
    </li>
  </ul>
  <svg class="stripes" width="200" height="24" aria-hidden="true">
    <polygon points="8,0 24,0 18,6 2,6" fill="#7cc242"/>
    <polygon points="30,0 46,0 40,6 24,6" fill="#7cc242"/>
    <polygon points="44,10 200,10 200,24 30,24" fill="#1f64c0"/>
  </svg>
</section>

<div class="production-notes">
  <p>300 dpi resulation</p>
  <p>cmyk color for print</p>
  <p>rgb for web</p>
  <p>Ai and psd</p>
  <p>and</p>
  <p>0.25 blend option</p>
</div>

</body>
</html>
```